Nine Phase Ledger Roadmap Talk

I would like a flyer to hand out to participants at the speeches that we give. We are a CPA firm that specializes in entrepreneurs and realtors. We would like a flyer that looks crisp and clean, that integrates our logo and our company colors (shades of blue & gold). We would like the wording to be as laid out in the attached documents, but design is up to you. We would like a picture to go along with each point and are open to ideas. The flyer should be one page, preferably just the front.

Colors
3176b5
fee18a

Requirements
Must have
• Our logo and the wording supplied.
• A picture to go along with each topic.
Nice to have
• Images that pop, clean look, professional.
Should not have
• Look messy.

```html
<!DOCTYPE html>
<html lang="en">
<head>
<meta charset="utf-8">
<title>Nine Phase Ledger Roadmap Talk – Agenda</title>
<link rel="stylesheet" href="https://fonts.googleapis.com/css2?family=Open+Sans:wght@700;800&family=Lato:ital,wght@0,400;0,700;1,700&family=Arimo:wght@400&display=swap">
<style>
  :root{
    --navy-deep:#222938;
    --navy-mid:#2e3b52;
    --navy-soft:#3f5b80;
    --sky:#8ed3f3;
    --ring:#4f93d8;
    --line:#5a9ad9;
    --gold:#fee18a;
    --brand-blue:#3176b5;
    --band:#86c6e6;
    --white:#ffffff;
    --ink:#1d2a40;
  }
  *{margin:0;padding:0;box-sizing:border-box}
  html,body{width:894px;height:1200px;overflow:hidden;background:var(--navy-deep)}
  .flyer{position:relative;width:894px;height:1200px;overflow:hidden;
    background:linear-gradient(100deg,var(--navy-deep) 0%,var(--navy-mid) 45%,var(--navy-soft) 100%);
    font-family:"Arimo",Arial,sans-serif;color:var(--white)}
  .brand{position:absolute;left:72px;top:78px;width:250px;text-align:center}
  .brand-name{font-family:"Lato",sans-serif;font-weight:700;font-size:31px;letter-spacing:1px;color:var(--gold);line-height:1.05;text-transform:uppercase}
  .brand-tag{margin-top:12px;font-family:"Lato",sans-serif;font-style:italic;font-weight:700;font-size:13px;color:var(--white)}
  .headline{position:absolute;left:474px;top:40px;font-family:"Open Sans",sans-serif;font-weight:800;line-height:1}
  .headline .lead{display:flex;align-items:flex-end}
  .headline .numeral{font-size:190px;color:var(--sky);letter-spacing:-8px;line-height:150px}
  .headline .phase{font-size:78px;color:var(--sky);margin-left:6px;margin-bottom:-4px}
  .headline .sub{font-family:"Lato",sans-serif;font-weight:400;font-size:44px;color:var(--sky);margin-top:14px;letter-spacing:.5px}
  .headline .main{font-size:44px;color:var(--white);margin-top:2px;line-height:44px}
  .flow{position:absolute;inset:0}
  .step-no{position:absolute;width:130px;height:30px;display:flex;align-items:center;justify-content:center}
  .step-no::before{content:"";position:absolute;left:0;right:0;top:15px;height:1px;background:#9aa8bd}
  .step-no span{position:relative;width:29px;height:29px;border-radius:50%;background:var(--white);color:var(--brand-blue);
    font-family:"Open Sans",sans-serif;font-weight:800;font-size:19px;display:flex;align-items:center;justify-content:center}
  .step-text{position:absolute;font-size:14.6px;line-height:17.6px;text-align:justify;color:var(--white)}
  .col-left{left:72px;width:244px}
  .col-right{left:604px;width:230px}
  .motto{position:absolute;left:0;right:0;top:1042px;text-align:center;font-family:"Lato",sans-serif;font-style:italic;font-weight:700;font-size:25px}
  .contact-band{position:absolute;left:0;right:0;top:1089px;height:79px;background:var(--band);text-align:center;color:var(--ink);padding-top:11px}
  .contact-band .firm{font-family:"Lato",sans-serif;font-size:17px;font-weight:400}
  .contact-band .firm b{font-weight:700}
  .contact-band .addr,.contact-band .phones{font-size:12.5px;margin-top:3px}
  .phones span{margin:0 12px}
  .contact-strip{position:absolute;left:0;right:0;top:1168px;height:32px;display:flex;justify-content:center;align-items:center;gap:26px;font-size:11.5px;background:var(--navy-mid)}
</style>
</head>
<body>
<main class="flyer">

  <div class="brand">
    <div class="brand-name">Clearline Figures</div>
    <div class="brand-tag">A Professional Accounting Corporation</div>
  </div>

  <h1 class="headline">
    <div class="lead"><span class="numeral">9</span><span class="phase">PHASE</span></div>
    <div class="sub">LEDGER ROADMAP</div>
    <div class="main">TALK<br>AGENDA</div>
  </h1>

  <svg class="flow" width="894" height="1200" viewBox="0 0 894 1200">
    <g fill="none" stroke="var(--line)" stroke-width="4" stroke-linecap="round">
      <path d="M387 0 V322"/>
      <path d="M387 434 V452 Q387 464 399 464 H475"/>
      <path d="M531 520 V553 Q531 565 519 565 H443"/>
      <path d="M387 621 V652 Q387 664 399 664 H475"/>
      <path d="M531 720 V743 Q531 755 519 755 H443"/>
      <path d="M387 811 V839 Q387 851 399 851 H475"/>
      <path d="M531 907 V929 Q531 941 519 941 H443"/>
    </g>
    <g fill="var(--white)" stroke="var(--ring)" stroke-width="6">
      <circle cx="387" cy="378" r="54"/>
      <circle cx="531" cy="464" r="54"/>
      <circle cx="387" cy="565" r="54"/>
      <circle cx="531" cy="664" r="54"/>
      <circle cx="387" cy="755" r="54"/>
      <circle cx="531" cy="851" r="54"/>
      <circle cx="387" cy="941" r="54"/>
    </g>
    <!-- 1: money with cut -->
    <g stroke="var(--navy-deep)" fill="none" stroke-width="3">
      <rect x="358" y="354" width="48" height="44" stroke-dasharray="6 4"/>
      <circle cx="381" cy="376" r="11" fill="var(--navy-deep)"/>
      <path d="M408 366 L420 394 M420 366 L408 394"/>
    </g>
    <text x="381" y="382" text-anchor="middle" font-family="Open Sans,sans-serif" font-weight="800" font-size="15" fill="var(--white)">$</text>
    <!-- 2: house over hand -->
    <g stroke="var(--navy-deep)" fill="none" stroke-width="3.5" stroke-linejoin="round">
      <path d="M512 462 L531 444 L550 462 V478 H512 Z"/>
      <path d="M506 488 H522 L534 494 H554 Q560 494 558 498 L540 506 H506"/>
    </g>
    <text x="531" y="474" text-anchor="middle" font-family="Open Sans,sans-serif" font-weight="800" font-size="17" fill="var(--navy-deep)">$</text>
    <!-- 3: magnifier over receipt -->
    <g stroke="var(--navy-deep)" fill="none" stroke-width="3.5" stroke-linecap="round">
      <circle cx="380" cy="558" r="17"/>
      <path d="M392 570 L408 586" stroke-width="6"/>
      <path d="M373 551 H387 M373 558 H387 M373 565 H382"/>
    </g>
    <!-- 4, 5, 6: illustrated groups -->
    <circle cx="531" cy="664" r="36" fill="var(--navy-deep)" role="img" aria-label="Icon of a planning meeting around a table"/>
    <circle cx="387" cy="755" r="36" fill="var(--navy-deep)" role="img" aria-label="Icon of a family with a savings jar"/>
    <circle cx="531" cy="851" r="36" fill="var(--navy-deep)" role="img" aria-label="Icon of a college graduate"/>
    <!-- 7: rising chart -->
    <g fill="var(--navy-deep)">
      <rect x="360" y="950" width="8" height="14"/>
      <rect x="372" y="942" width="8" height="22"/>
      <rect x="384" y="934" width="8" height="30"/>
      <rect x="396" y="926" width="8" height="38"/>
      <path d="M356 944 L376 926 L388 936 L408 916 L402 912 H418 V928 L413 922 L388 946 L376 936 L360 950 Z"/>
    </g>
  </svg>

  <div class="step-no" style="left:128px;top:268px"><span>1</span></div>
  <p class="step-text col-left" style="top:314px">We will first show you how to eliminate much of your self-employment tax on your return by converting your business into an S Corporation. A business owner making over $120,000 per year can save about $12,000 per year by doing this.</p>

  <div class="step-no" style="left:652px;top:365px"><span>2</span></div>
  <p class="step-text col-right" style="top:411px">We will show you how to get tax free income from your corporation by renting you home to the corporation for the board meetings. Many of our clients are getting up to $21,000 in tax free income which could put $8,400 cash into your pocket.</p>

  <div class="step-no" style="left:128px;top:481px"><span>3</span></div>
  <p class="step-text col-left" style="top:526px">We will show you the easiest way to track your expenses so that the only thing you will have to do to have rock solid books is to take a picture of the receipt and throw it away. It doesn't get any better than that.</p>

  <div class="step-no" style="left:652px;top:580px"><span>4</span></div>
  <p class="step-text col-right" style="top:624px">Next, we show you the importance of tax planning and why it is critical to meet with your CPA before the end of the year and not just when you do your tax preparation.</p>

  <div class="step-no" style="left:128px;top:670px"><span>5</span></div>
  <p class="step-text col-left" style="top:720px">We will show you how to hire your children and get $7,500 per child tax free. This will save you $3,000 per child in income tax reduction.</p>

  <div class="step-no" style="left:652px;top:758px"><span>6</span></div>
  <p class="step-text col-right" style="top:802px">We will discuss how to make your child's college education tax deductible. With college cost spiraling out of control this is a biggie. Most of our clients have a savings of about $12,000 per year of college.</p>

  <div class="step-no" style="left:128px;top:838px"><span>7</span></div>
  <p class="step-text col-left" style="top:884px">Our grand finale is to show you how to use, not one, but two corporations to get a several hundred thousand dollar tax deferral, get an interest free loan from the government and use that money to grow your business and your wealth.</p>

  <p class="motto">If they drive by with a machine gun you don't have to stand up.</p>

  <footer>
    <div class="contact-band">
      <div class="firm"><b>CLEARLINE FIGURES,</b> A Professional Accounting Corporation</div>
      <div class="addr">820 N. Orchard Ave, Ste. B, Lodi, CA 95240</div>
      <div class="phones"><span>&#9742; 209-555-0142</span><span>&#9113; 209-555-0178</span></div>
    </div>
    <div class="contact-strip">
      <span>&#9993; Dana@clearlinefigurescpas.com</span>
      <span>&#9993; Morgan@clearlinefigurescpas.com</span>
      <span>&#9737; www.clearlinefigurescpa.com</span>
    </div>
  </footer>

</main>
</body>
</html>
```